Luxury Real Estate Website, Midwest, United States

We need web design services for a luxury website. We need IDX Integration with our MLS. We want this to be a very simple website with amazing graphics. We want it to link up with our PostLoop account in order to generate leads through a "More Information" Pop up on the main page. We want the main page to be covered with one large graphic that is a rolling slideshow of active listings of $400,000 and up from the IDX Integration. We need this website to give a very exclusive and sleek look. Lots of black is good... I will upload our logos in Black and Silver. We will also need an "About" page that we are going to call "Qeno Info". We want our graphics to be extremely impressive. Keep in mind, we are a company in the Midwest of the United States, and our real estate has a different look than homes in California or Florida. We need graphics that are realistic for the Midwest, yet still high-end.
Target Market(s)
Luxury Homeowners in the Midwest United States. The graphics needs to be pristine.
Industry/Entity Type
Real Estate
Coding
Coded - Design and coding required
Number of Pages Required
3 page
Requirements
Must have
- Large graphics with IDX Integration. The photos of real estate need to represent real estate that is common in the Midwest, United States. We also need PostLoop integration. We need a pop up that is titled "My Free Market Analysis" that makes them fill out a contact form asking for Full Name, Email Address, Phone Number and Address. This needs to be a pop up on the front page and will integrate with our PostLoop account. We also need a page called "About Qe No Home". And another page where clients can download informational PDFs. The main component needs to be a front page search engine connected with the IDX to access active listings from our MLS. I attached our logos and a sample front page of a website. I would love for ours to look similar.
Nice to have
- Lake House photos on midwest lakes are a plus.
Should not have
- Should not have clutter. This website needs to be clean, luxurious and exclusive.

```html
<!DOCTYPE html>
<html lang="en">
<head>
<meta charset="utf-8">
<title>Crestline Realty Group</title>
<link rel="stylesheet" href="https://fonts.googleapis.com/css2?family=Josefin+Sans:wght@400;600;700&family=Open+Sans:wght@400;600&display=swap">
<style>
:root{
  --ink:#1c1c1e;
  --paper:#ffffff;
  --mist:#f1f1f2;
  --line:#d9d9dc;
  --muted:#7a7a80;
  --accent:#2f7f9a;
  --dark:#141416;
  --veil:rgba(8,8,10,.74);
  --sky:#6fa6d6;
  --lake:#2e6f8a;
  --grass:#6a9a3c;
  --wood:#6b4a2e;
}
*{box-sizing:border-box;margin:0;padding:0}
html,body{width:1200px;height:3797px;overflow:hidden}
body{position:relative;background:var(--paper);font-family:"Open Sans",Arial,sans-serif;color:var(--ink)}
.abs{position:absolute}
.heading{font-family:"Josefin Sans",Helvetica,sans-serif;font-weight:700;letter-spacing:1px;text-transform:uppercase;color:var(--ink)}
.num{font-family:"Josefin Sans",Helvetica,sans-serif;font-weight:600;color:#c9c9cd;font-size:64px}
.body-text{font-size:14px;line-height:26px;color:var(--muted)}
.photo{position:absolute}
.btn-outline{position:absolute;border:2px solid var(--ink);font-family:"Josefin Sans",sans-serif;font-weight:600;font-size:14px;letter-spacing:1px;display:flex;align-items:center;justify-content:center;gap:6px;text-transform:uppercase}
.btn-outline i{width:12px;height:12px;border-radius:50%;background:var(--ink);display:inline-block}

/* header */
.site-header{left:0;top:0;width:1200px;height:96px;background:var(--paper);z-index:2}
.brand{left:96px;top:30px;font-family:"Josefin Sans",sans-serif;font-weight:700;font-size:26px;letter-spacing:2px;color:var(--ink);display:flex;align-items:center;gap:10px}
.brand span.mark{width:14px;height:14px;background:var(--ink)}
.nav{right:96px;top:40px;display:flex;gap:26px;font-family:"Josefin Sans",sans-serif;font-weight:600;font-size:14px;letter-spacing:1px;color:var(--ink)}

/* hero */
.hero{left:0;top:96px;width:1200px;height:557px;background:linear-gradient(180deg,#7a9fbf 0%,#a9b9a0 40%,#5d7a3c 70%,#3f5426 100%)}
.hero-title{left:0;top:300px;width:1200px;text-align:center;font-family:"Josefin Sans",sans-serif;font-weight:700;font-size:50px;color:#fff;letter-spacing:2px}
.arrow{width:34px;height:34px;border-radius:50%;background:rgba(0,0,0,.5)}

/* cards */
.card-caption{position:absolute;background:#fff;font-family:"Josefin Sans",sans-serif;font-weight:600;font-size:13px;line-height:20px;padding:12px 14px;color:var(--ink)}
.tab{font-family:"Josefin Sans",sans-serif;font-weight:600;font-size:13px;letter-spacing:1px;color:var(--ink)}
.field{position:absolute;border:1px solid var(--line);background:#fff;font-size:13px;color:var(--muted);padding:10px 14px}

/* footer */
.footer{left:0;top:3487px;width:1200px;height:240px;background:linear-gradient(180deg,#3a3a3e,#202024)}
.footer h4{font-family:"Josefin Sans",sans-serif;font-weight:700;font-size:17px;color:#fff;letter-spacing:1px}
.footer p{font-size:13px;color:#d6d6da}
.bottom-bar{left:0;top:3727px;width:1200px;height:70px;background:var(--dark)}
.social{width:40px;height:40px;border-radius:50%;background:#55555c}

/* veil + popup */
.veil{left:0;top:0;width:1200px;height:3797px;background:var(--veil);z-index:5}
.popup{left:185px;top:410px;width:797px;height:443px;border:8px solid #e9edf2;z-index:6;background:linear-gradient(180deg,#5b8fc6 0%,#a7c4de 30%,#76a24a 52%,#2d6a86 70%,#1f4f66 100%)}
.popup-brand{left:0;top:50px;width:100%;text-align:center;font-family:"Josefin Sans",sans-serif;font-weight:700;font-size:28px;color:#fff;letter-spacing:2px}
.popup-title{left:0;top:134px;width:100%;text-align:center;font-family:"Josefin Sans",sans-serif;font-weight:700;font-size:26px;color:#fff;letter-spacing:1px}
.popup-sub{left:0;top:170px;width:100%;text-align:center;font-size:13px;color:#fff}
.popup .field{border:none;font-size:12px;color:#555;padding:12px 14px;height:40px}
.popup-submit{left:106px;top:324px;width:169px;height:45px;background:var(--dark);color:#fff;font-family:"Josefin Sans",sans-serif;font-weight:700;font-size:15px;display:flex;align-items:center;justify-content:center;letter-spacing:1px}
.partner{left:470px;top:332px;display:flex;align-items:center;gap:10px;font-family:"Josefin Sans",sans-serif;font-weight:700;font-size:26px;color:#fff}
.partner i{width:26px;height:26px;border-radius:50%;background:#fff;display:block}
.close{left:962px;top:380px;width:52px;height:52px;border-radius:50%;background:#fff;z-index:7;display:flex;align-items:center;justify-content:center}
.close span{width:38px;height:38px;border-radius:50%;background:var(--dark);display:flex;align-items:center;justify-content:center}
</style>
</head>
<body>

<header class="abs site-header">
  <div class="abs brand"><span class="mark"></span>CRESTLINE</div>
  <nav class="abs nav"><span>HOME</span><span>QENO INFO</span><span>ABOUT QE NO HOME</span><span>DOWNLOADS</span><span>CONTACT US</span></nav>
</header>

<section class="abs hero" role="img" aria-label="Slideshow photo of a timber lake house on a green hillside">
</section>
<div class="abs hero-title">FIND YOUR NEW HOME</div>
<div class="abs arrow" style="left:16px;top:356px"></div>
<div class="abs arrow" style="left:1150px;top:356px"></div>

<!-- 01 properties -->
<div class="abs num" style="left:60px;top:740px">01</div>
<div class="abs heading" style="left:140px;top:762px;font-size:32px">PROPERTIES</div>
<p class="abs body-text" style="left:96px;top:832px;width:470px">Every listing in our collection is chosen for its setting, its craft and its quiet sense of place. From lakefront retreats to wooded estates, we show homes that feel at ease in the Midwest landscape and bring you closer to the life you picture living there.</p>
<div class="btn-outline" style="left:96px;top:1018px;width:160px;height:42px">READ MORE <i></i></div>
<div class="abs" style="left:632px;top:746px;width:472px;height:292px;border:1px solid var(--line)"></div>
<svg class="abs" style="left:640px;top:870px" width="30" height="130" viewBox="0 0 30 130">
  <rect x="3" y="8" width="24" height="10" fill="#555"/><rect x="3" y="4" width="4" height="18" fill="#555"/>
  <rect x="5" y="52" width="20" height="12" rx="3" fill="#555"/><rect x="8" y="64" width="3" height="6" fill="#555"/>
  <rect x="3" y="100" width="24" height="12" rx="4" fill="#555"/><circle cx="9" cy="113" r="3" fill="#555"/><circle cx="21" cy="113" r="3" fill="#555"/>
</svg>
<div class="photo" style="left:684px;top:780px;width:379px;height:278px;background:linear-gradient(180deg,#9fb8cf,#c9b89a 55%,#6d7f4a)" role="img" aria-label="Photo of a large stone and shingle lakeside home"></div>

<div class="photo" style="left:101px;top:1122px;width:312px;height:223px;background:linear-gradient(180deg,#a8c1d8,#8da56a 60%,#4d6a3c)" role="img" aria-label="Photo of a brick estate with lawn and pond"></div>
<div class="photo" style="left:443px;top:1122px;width:312px;height:223px;background:linear-gradient(180deg,#dfe6ec,#8fa7b6 50%,#3a3a3a)" role="img" aria-label="Photo of a dining terrace overlooking a lake"></div>
<div class="photo" style="left:785px;top:1122px;width:311px;height:223px;background:linear-gradient(180deg,#7fa7c8,#6f8a5a 50%,#6a4a32)" role="img" aria-label="Photo of a wooden lake house with a fountain"></div>
<div class="abs" style="left:570px;top:1380px;display:flex;gap:10px">
  <span style="width:12px;height:12px;border-radius:50%;background:var(--line)"></span>
  <span style="width:12px;height:12px;border-radius:50%;background:var(--ink)"></span>
  <span style="width:12px;height:12px;border-radius:50%;background:var(--line)"></span>
</div>

<!-- 02 about -->
<div class="abs" style="left:72px;top:1590px;width:380px;height:280px;border:1px solid var(--line)"></div>
<div class="photo" style="left:96px;top:1615px;width:410px;height:279px;background:linear-gradient(180deg,#8a5a3c,#c9c2b6 45%,#7a8a8f)" role="img" aria-label="Photo of a covered patio lounge with sofas"></div>
<div class="abs heading" style="left:734px;top:1596px;font-size:32px">ABOUT QE NO HOME</div>
<div class="abs num" style="left:1090px;top:1575px">02</div>
<div class="abs" style="left:656px;top:1690px;display:flex;gap:34px">
  <span class="tab">ROOM DIMENSION</span><span class="tab" style="color:var(--accent)">INTERIOR ROOM</span><span class="tab">EXTERIOR ROOM</span>
</div>
<p class="abs body-text" style="left:570px;top:1752px;width:532px">Each residence is measured, photographed and walked through room by room so you know what to expect before you arrive. Browse interiors with natural light, open kitchens and warm living spaces, then compare exterior details such as decks, docks and gardens designed for long summer evenings on the water.</p>

<!-- 03 featured -->
<div class="abs num" style="left:55px;top:2076px">03</div>
<div class="abs heading" style="left:145px;top:2097px;font-size:32px">FEATURED HOMES</div>
<p class="abs body-text" style="left:96px;top:2172px;width:260px">Hand-picked homes from across the region, selected for their location, quality and character. Each one is ready for a private showing.</p>
<div class="btn-outline" style="left:96px;top:2378px;width:136px;height:42px">VIEW ALL <i></i></div>

<div class="photo" style="left:372px;top:2185px;width:231px;height:170px;background:linear-gradient(180deg,#7fa1bf,#4d6e3a 55%,#2d5f72)" role="img" aria-label="Photo of a lakeside home with pool"></div>
<div class="card-caption" style="left:372px;top:2355px;width:231px">Luxury Real Estate Home From<br>Midwest, United States</div>
<div class="photo" style="left:620px;top:2185px;width:231px;height:170px;background:linear-gradient(180deg,#9ab7cf,#5f7f44 50%,#8a6a4a)" role="img" aria-label="Photo of a wooden dock on a lake"></div>
<div class="card-caption" style="left:620px;top:2355px;width:231px">Luxury Real Estate Home From<br>Midwest, United States</div>
<div class="photo" style="left:868px;top:2185px;width:231px;height:170px;background:linear-gradient(180deg,#a7c2d8,#6f8f4c 50%,#3c6a7f)" role="img" aria-label="Photo of a lake house among trees"></div>
<div class="card-caption" style="left:868px;top:2355px;width:231px">Luxury Real Estate Home From<br>Midwest, United States</div>

<!-- 04 blog -->
<section class="photo" style="left:0;top:2519px;width:1200px;height:406px;background:linear-gradient(180deg,#4a6a86,#6f8ea4 35%,#3e5a3a 60%,#8a6e52)" role="img" aria-label="Photo of a deck with lounge chairs overlooking a mountain lake"></section>
<div class="abs heading" style="left:784px;top:2618px;font-size:30px;color:#fff">FROM BLOG POST</div>
<div class="abs num" style="left:1100px;top:2596px;color:#e6e6ea">04</div>
<div class="abs" style="left:658px;top:2717px;width:438px;height:187px;background:rgba(20,20,24,.72);padding:22px 24px">
  <div style="text-align:right;font-size:13px;color:#fff;margin-bottom:8px">21 Apr 2018</div>
  <p style="font-size:13px;line-height:23px;color:#e0e0e4">Spring brings fresh listings to the lakes. Learn what buyers are looking for this season and how to prepare your home to stand out in a competitive market.</p>
</div>
<div class="abs arrow" style="left:16px;top:2735px"></div>
<div class="abs arrow" style="left:1150px;top:2735px"></div>

<!-- contact -->
<section class="abs" style="left:0;top:2925px;width:1200px;height:562px;background:var(--mist)"></section>
<div class="abs heading" style="left:0;top:3080px;width:1200px;text-align:center;font-size:30px">STAY IN OUR TOUCH!</div>
<p class="abs" style="left:0;top:3134px;width:1200px;text-align:center;font-size:13px;color:var(--muted)">If you have any questions, please leave us a message and we will get back to you soon.</p>
<div class="field" style="left:203px;top:3185px;width:260px;height:40px">Your Name</div>
<div class="field" style="left:476px;top:3185px;width:251px;height:40px">Email Address</div>
<div class="field" style="left:742px;top:3185px;width:258px;height:40px">Phone</div>
<div class="field" style="left:203px;top:3241px;width:797px;height:72px">Message</div>
<div class="abs" style="left:519px;top:3347px;width:165px;height:42px;background:var(--dark);color:#fff;font-family:'Josefin Sans',sans-serif;font-weight:700;font-size:14px;letter-spacing:1px;display:flex;align-items:center;justify-content:center">SUBMIT NOW</div>

<!-- footer -->
<footer class="abs footer" role="img" aria-label="Faint photo of a lake house behind the footer">
  <div class="abs" style="left:101px;top:96px;font-family:'Josefin Sans',sans-serif;font-weight:700;font-size:40px;color:#fff;letter-spacing:2px">CRESTLINE</div>
  <h4 class="abs" style="left:519px;top:52px">CRESTLINE REALTY GROUP</h4>
  <svg class="abs" style="left:519px;top:98px" width="14" height="120" viewBox="0 0 14 120">
    <path d="M7 0a6 6 0 0 1 6 6c0 5-6 11-6 11S1 11 1 6a6 6 0 0 1 6-6z" fill="#d6d6da"/>
    <rect x="2" y="44" width="10" height="14" rx="2" fill="#d6d6da"/>
    <rect x="1" y="88" width="12" height="9" fill="#d6d6da"/>
  </svg>
  <p class="abs" style="left:552px;top:98px">1234 Lakeshore Drive, Fishers, IN 46037</p>
  <p class="abs" style="left:552px;top:142px">(317) 555-0148</p>
  <p class="abs" style="left:552px;top:184px">hello@crestlinerealty.com</p>
  <h4 class="abs" style="left:886px;top:52px">OPENING TIME</h4>
  <p class="abs" style="left:886px;top:98px;line-height:24px">Monday - Friday 9am to 6pm<br>Saturday 10am to 4pm<br>Sunday Closed</p>
</footer>
<div class="abs bottom-bar">
  <p class="abs" style="left:101px;top:26px;font-size:13px;color:#b8b8bd">© Copyright 2018 Crestline Realty Group. All Rights Reserved.</p>
  <div class="abs" style="left:940px;top:15px;display:flex;gap:10px">
    <span class="social"></span><span class="social"></span><span class="social"></span><span class="social"></span>
  </div>
</div>

<!-- dim layer + market analysis popup -->
<div class="abs veil"></div>
<div class="abs popup" role="img" aria-label="Background photo of a mountain lake with pine trees and chalets">
  <div class="abs popup-brand">CRESTLINE</div>
  <div class="abs popup-title">MY FREE MARKET ANALYSIS</div>
  <div class="abs popup-sub">Everyone has a choice. I pick my choice.</div>
  <div class="field" style="left:106px;top:210px;width:281px">Full Name</div>
  <div class="field" style="left:397px;top:210px;width:281px">Phone Number</div>
  <div class="field" style="left:106px;top:261px;width:281px">Email Address</div>
  <div class="field" style="left:397px;top:261px;width:281px">Address</div>
  <div class="abs popup-submit">SUBMIT NOW</div>
  <div class="abs partner"><i></i>PostLoop</div>
</div>
<div class="abs close"><span>
  <svg width="16" height="16" viewBox="0 0 16 16"><path d="M2 2l12 12M14 2L2 14" stroke="#fff" stroke-width="3"/></svg>
</span></div>

</body>
</html>
```